Norrell Advisory WA Business Card

Create an interesting, eye catching and colourful two sided business card. We are a business consulting operation assisting SME's improve all areas of their business. We provide consulting services to assist SME's to create a culture of continuous improvement, making a positive difference in the business. Our tag line is Small changes, big rewards. We want to create a well recognised, innovative brand that can be continued throughout our website, social media and email correspondence.

Target Market(s)

Small to Medium Enterprise Business Owners

Industry/Entity Type

Business Consultant

Contact Information for Business Card

Name of Business: Norrell Advisory - Clear Plans Real Progress
Derek Holloway Ph 0407385510 Megan Holloway Ph 0407913847
Email norrelladvisorywa@mailbox-example.com
Web address TBA
FaceBook page TBA

BACKSIDE OF CARD

Providing assistance with:

• Organisation & Efficiency
• Revenue generation & Marketing
• Financial Management
• Production quality & delivery
• Systems & Process documentation
• Exit Strategy

Font styles to use
Other font styles liked:
• Calibri

Colors

Designer to choose colors to be used in the design.

Requirements
Must have
• Calibri font

```html
<!DOCTYPE html>
<html lang="en">
<head>
<meta charset="utf-8">
<title>Norrell Advisory WA Business Card</title>
<link rel="stylesheet" href="https://fonts.googleapis.com/css2?family=Open+Sans:ital,wght@0,400;0,700;1,700&display=swap">
<style>
  :root {
    --backdrop: #e6e6e6;
    --card: #ffffff;
    --ink: #2f2f2f;
    --ink-soft: #4a4a4a;
    --brand-blue: #1a73b5;
    --rule: #555555;
    --mark: #3a9ad6;
    --pattern-a: #4a5a3a;
    --pattern-b: #6b3a32;
    --pattern-c: #34506a;
    --pattern-d: #7a6a34;
  }
  * { box-sizing: border-box; margin: 0; padding: 0; }
  html, body {
    width: 1125px; height: 1200px; overflow: hidden;
    background: var(--backdrop);
    font-family: "Open Sans", Arial, sans-serif;
  }
  .canvas { position: relative; width: 1125px; height: 1200px; }
  .card {
    position: absolute; left: 171px; width: 826px; height: 472px;
    background: var(--card);
  }
  .card--front { top: 106px; }
  .card--back { top: 640px; }

  .brand { position: absolute; left: 50px; top: 90px; width: 350px; text-align: center; }
  .brand__mark {
    display: block; width: 140px; height: 140px; margin: 0 auto 18px;
    background: var(--mark); border-radius: 12px;
  }
  .brand__name { font-size: 29px; font-weight: 700; color: var(--ink); letter-spacing: 0.3px; line-height: 1; }
  .brand__tagline { margin-top: 8px; font-size: 15.5px; color: var(--ink-soft); letter-spacing: 2.6px; line-height: 1; }

  .people { position: absolute; left: 445px; top: 82px; }
  .person { margin-bottom: 14px; }
  .person__name { font-size: 27px; font-weight: 700; color: var(--brand-blue); line-height: 1.1; }
  .person__phone { font-size: 16px; font-weight: 700; color: var(--ink-soft); line-height: 1.3; }

  .contacts { position: absolute; left: 445px; top: 225px; list-style: none; }
  .contacts li { display: flex; align-items: center; font-size: 16.5px; color: var(--ink-soft); line-height: 25px; }
  .contacts svg { width: 18px; height: 18px; margin-right: 12px; flex: none; }

  .services { position: absolute; left: 56px; right: 52px; top: 340px; text-align: center; }
  .services__heading { display: flex; align-items: center; gap: 6px; }
  .services__heading::before, .services__heading::after {
    content: ""; flex: 1; height: 1px; background: var(--rule);
  }
  .services__title { font-size: 26px; font-weight: 700; font-style: italic; color: var(--brand-blue); }
  .services__list { margin-top: 6px; font-size: 18px; color: var(--ink-soft); line-height: 25px; }
  .dot { color: var(--brand-blue); }

  .back-fill {
    position: absolute; inset: 0;
    background:
      linear-gradient(135deg, var(--pattern-b) 0%, var(--pattern-a) 30%, var(--pattern-c) 55%, var(--pattern-d) 80%, var(--pattern-b) 100%);
  }
</style>
</head>
<body>
<main class="canvas">
  <section class="card card--front">
    <div class="brand">
      <span class="brand__mark"></span>
      <div class="brand__name">NORRELL ADVISORY</div>
      <div class="brand__tagline">CLEAR PLANS REAL PROGRESS</div>
    </div>

    <div class="people">
      <div class="person">
        <div class="person__name">DEREK HOLLOWAY</div>
        <div class="person__phone">0407385510</div>
      </div>
      <div class="person">
        <div class="person__name">MEGAN HOLLOWAY</div>
        <div class="person__phone">0407913847</div>
      </div>
    </div>

    <ul class="contacts">
      <li>
        <svg viewBox="0 0 18 18" aria-hidden="true"><rect x="1" y="4" width="16" height="11" fill="var(--brand-blue)"/><path d="M1 4l8 6 8-6" fill="none" stroke="#fff" stroke-width="1.4"/></svg>
        norrelladvisorywa@mailbox-example.com
      </li>
      <li>
        <svg viewBox="0 0 18 18" aria-hidden="true"><circle cx="9" cy="9" r="8" fill="var(--brand-blue)"/><ellipse cx="9" cy="9" rx="3.5" ry="8" fill="none" stroke="#fff" stroke-width="1.2"/><path d="M1 9h16" stroke="#fff" stroke-width="1.2"/></svg>
        www.norrelladvisorywa.com
      </li>
      <li>
        <svg viewBox="0 0 18 18" aria-hidden="true"><rect x="1" y="1" width="16" height="16" fill="var(--brand-blue)"/></svg>
        norrelladvisorywa
      </li>
    </ul>

    <div class="services">
      <div class="services__heading"><span class="services__title">Providing assistance with</span></div>
      <p class="services__list">
        Organisation &amp; Efficiency <span class="dot">•</span> Revenue generation &amp; Marketing <span class="dot">•</span> Financial Management<br>
        Production quality &amp; delivery <span class="dot">•</span> Systems &amp; Process documentation <span class="dot">•</span> Exit Strategy
      </p>
    </div>
  </section>

  <section class="card card--back">
    <div class="back-fill" role="img" aria-label="Decorative all-over pattern of interlocking pieces in muted red, green, blue and ochre"></div>
  </section>
</main>
</body>
</html>
```